Im want a website LIKE VRX's and FleetHollow.com's with product payment options like Trenzo's

I need a website LIKE VRX with a header made EXACTLY LIKE THAT OF FLEETHOLLOWS .

The front page photo should be like that of FLEETHOLLOW's webpage as well.

The name of the website will be called "M.K. (Caldera Key)".

We will be targeting ALL MARKETS in a small town in central Panama and charging businesses "listing fees" like a phone book does but also providing informational blogs, news, and other interesting activities.

THIS IS A MULTI PAGE WEBSITE

THIS IS WHERE VRX's website meets Brivelle/FleetHollow.

Once the layout is built I will tweak and modify, add information, and upload items for sale.

Here is a list of specific categories that should be listed out above the front page header image/search bar

-- Home -- News -- Travel -- Activities -- Shop & Dine -- Store -- More... --

These categories should be spread across the bottom of the page in three sections:

WHATS SO GREAT ABOUT (Caldera Key),
HAND PICKED TOURS
ACTIVITIES etc.

Also lets use www.Trenzo.example 's
"HOT DESTINATIONS"
"BEAT THE BEST PRICES IN BOQUETE"
"OCTOBERS INSIDER PICKS"
"TOP DESTINATIONS"
and spread them in four sections side-by-side near the bottom of the page.

Overall I would like to see the finished product to be something LIKE VRX's and FleetHollows.

WE NEED ONLINE PAYMENT OPTIONS LIKE BRIVELLE'S WEBSITE HAS

This will be a desktop website but should be very mobile friendly as well.

-rodmund

P.S. Good luck!

If it isn't already too late to change the website name, the name of the website should be "Caldera Key". Added Friday, October 9, 2015

What do you guys think the budget should be to win this? Added Saturday, October 10, 2015

www.palmorra.example is the most amazing simple site. Whoever can make me a replica with my specifications will win immediately!!!! Added Sunday, October 18, 2015

OMG www.palmorra.example is the bomb!So simple and elegant. Whoever can make me an EXACT REPLICA OF WWW.PALMORRA.EXAMPLE as my site with the specifications mentioned in my brief will take home the $825.00 immediately! Good luck amigos! Added Sunday, October 18, 2015

Does anybody know how to add recurring monthly billing options on this website? Added Sunday, October 18, 2015

ALL MARKETS

Product

Coded - Design and coding required

5+ page

• Coinvey payment options.
• I must be able to add and remove photos/text and video from the HTML files in the page.
• Be creative my friends, and may the odds be forever in your favor!
• I added some photos of a good layout for our page below.

```html
<!DOCTYPE html>
<html lang="en">
<head>
<meta charset="utf-8">
<title>Caldera Key</title>
<link rel="stylesheet" href="https://fonts.googleapis.com/css2?family=Montserrat:wght@400;600;700&family=Open+Sans:wght@400;600;700&display=swap">
<style>
:root{
  --blue:#1f8fd1;
  --teal:#2aa7c9;
  --navy:#17507f;
  --footer:#1e6aa6;
  --dark:#2b2f33;
  --ink:#3a3f44;
  --muted:#8a9096;
  --line:#e3e6e9;
  --orange:#f08a24;
  --star:#f5a623;
  --white:#ffffff;
}
*{box-sizing:border-box;margin:0;padding:0}
html,body{width:1200px;height:2400px;overflow:hidden}
body{font-family:"Open Sans",Arial,sans-serif;color:var(--ink);position:relative;background:#dfe9ee}
.backdrop{position:absolute;inset:0;background:linear-gradient(180deg,#3f8fc8 0%,#7fc1e6 18%,#c4e6f2 30%,#e9f1ef 45%,#f3efe6 70%,#e8e2d3 100%)}
.topbar{position:absolute;top:0;left:0;right:0;height:32px;background:rgba(20,28,36,.85);color:#d8dde2;font-size:12px;letter-spacing:1px;text-align:right;padding:8px 80px 0}
.page{position:absolute;top:32px;left:72px;width:1056px;height:2228px;background:var(--white);box-shadow:0 0 24px rgba(0,0,0,.15)}
.header{height:124px;display:flex;align-items:center;justify-content:space-between;padding:0 36px 0 16px}
.logo{font-family:"Montserrat",sans-serif;font-weight:700;font-size:30px;color:var(--navy);letter-spacing:1px}
.nav{display:flex;gap:6px;list-style:none;font-family:"Montserrat",sans-serif;font-size:13px;font-weight:600;letter-spacing:1px}
.nav li{padding:8px 14px;color:var(--ink)}
.nav li.active{border:2px solid var(--blue);color:var(--blue)}
.hero{position:relative;margin:0 16px;height:580px;background:linear-gradient(160deg,#c9d3d8 0%,#8e9aa2 35%,#6f7a80 55%,#b9c2c4 80%,#e2e4df 100%)}
.hero-caption{position:absolute;right:60px;top:240px;width:420px;background:rgba(42,167,201,.85);color:var(--white);font-family:"Montserrat",sans-serif;padding:22px 28px;text-align:right}
.hero-caption .kicker{font-size:20px;font-weight:600;letter-spacing:1px}
.hero-caption .title{font-size:26px;font-weight:700;line-height:1.3;margin-top:6px}
.arrow{position:absolute;top:270px;width:44px;height:44px;border-radius:50%;background:var(--white);display:flex;align-items:center;justify-content:center}
.arrow.prev{left:12px}.arrow.next{right:12px}
.dots{position:absolute;bottom:18px;left:50%;transform:translateX(-50%);display:flex;gap:10px}
.dots span{width:10px;height:10px;border-radius:50%;background:rgba(255,255,255,.6)}
.dots span.on{background:var(--white)}
.section-title{font-family:"Montserrat",sans-serif;font-weight:700;font-size:28px;text-align:center;color:var(--dark);letter-spacing:1px;margin-top:58px}
.tour-links{width:760px;margin:16px auto 0;text-align:center;font-size:13px;line-height:1.6;color:var(--ink)}
.tour-links a{color:var(--blue);text-decoration:none}
.cards{display:grid;grid-template-columns:repeat(4,232px);gap:28px 32px;margin:30px 0 0 16px}
.card{border:1px solid var(--line);height:384px;display:flex;flex-direction:column}
.card .photo{height:150px}
.card .body{padding:16px 14px;flex:1;display:flex;flex-direction:column}
.card h3{font-size:13px;font-weight:600;line-height:1.5;color:var(--ink);text-transform:uppercase}
.rating{display:flex;align-items:center;gap:8px;margin-top:12px;font-size:11px;color:var(--blue)}
.stars{color:var(--star);letter-spacing:1px;font-size:13px}
.viewer{font-size:12px;color:var(--muted);margin-top:10px}
.price{margin-top:auto;text-align:right;font-size:11px;color:var(--muted)}
.price strong{display:block;font-size:22px;color:var(--dark);font-weight:700}
.p1{background:linear-gradient(180deg,#6fb7e3,#2c78a8 60%,#8a6a4a)}
.p2{background:linear-gradient(135deg,#c98a4a,#7a4a22)}
.p3{background:linear-gradient(180deg,#9fc6e2,#4a8a3e 60%,#2f5f2a)}
.p4{background:linear-gradient(180deg,#3d6fa8,#c77a4a 55%,#5a3b2a)}
.p5{background:linear-gradient(180deg,#8fc4e8,#d9c7a6 60%,#3e7fa8)}
.p6{background:linear-gradient(180deg,#5fa8de,#e7e2d6 60%,#a69a86)}
.p7{background:linear-gradient(180deg,#4f9de0,#b9d7ec 60%,#5d8a4a)}
.p8{background:linear-gradient(180deg,#7fb5de,#8a6a5a 60%,#4a4a4a)}
.columns{display:grid;grid-template-columns:300px 300px 300px;gap:42px;margin:56px 0 0 36px}
.col-title{display:flex;align-items:center;gap:10px;font-family:"Montserrat",sans-serif;font-size:17px;font-weight:700;color:var(--dark);letter-spacing:1px;padding-bottom:14px;border-bottom:1px solid var(--line)}
.col-title svg{flex:none}
.dest{display:grid;grid-template-columns:1fr 1fr;gap:0 20px;margin-top:16px}
.dest ul,.picks,.deals{list-style:none}
.dest li,.picks li{font-size:12px;text-transform:uppercase;color:var(--ink);padding:7px 0;display:flex;align-items:center;gap:8px}
.dest li::before{content:"";width:0;height:0;border-left:5px solid var(--orange);border-top:4px solid transparent;border-bottom:4px solid transparent}
.beat p{font-size:13px;line-height:1.6;color:var(--muted);margin-top:14px}
.beat .row{display:flex;gap:16px;margin-top:16px}
.beat .thumb{width:110px;height:110px;background:linear-gradient(135deg,#d8e3ea,#9fb3c0)}
.deals li{font-size:12px;color:var(--blue);text-transform:uppercase;padding:5px 0}
.picks{margin-top:12px}
.picks li{color:var(--orange)}
.footer{position:absolute;left:0;right:0;top:2260px;height:140px;background:var(--footer);color:#dbe8f3;display:flex;padding:22px 72px 0 100px;gap:40px;font-size:11px}
.f-brand{display:flex;gap:16px;width:300px}
.f-badge{width:56px;height:56px;background:var(--orange);flex:none}
.f-brand h4,.footer h4{color:var(--white);font-size:14px;font-weight:600;margin-bottom:8px}
.f-brand p{line-height:1.5}
.f-brand .more{margin-top:8px;color:var(--white)}
.f-col{width:170px}
.f-col ul{list-style:none}
.f-col li{padding:2px 0;display:flex;align-items:center;gap:6px}
.f-col li::before{content:"";width:4px;height:4px;background:#dbe8f3;border-radius:50%}
.f-follow{margin-left:auto}
.social{display:flex;gap:8px}
.social span{width:26px;height:26px;border-radius:50%;background:#4fb0e3}
.social span:nth-child(2){background:#3b6fc0}
.social span:nth-child(3){background:#e0564a}
.social span:nth-child(4){background:#d84a8a}
.copy{margin-top:12px;line-height:1.5}
</style>
</head>
<body>
<div class="backdrop" role="img" aria-label="Tropical beach with palm trees and blue sky"></div>
<div class="topbar">LOGIN | REGISTER</div>

<div class="page">
  <header class="header">
    <div class="logo">CALDERA KEY</div>
    <ul class="nav">
      <li class="active">HOME</li><li>ABOUT US</li><li>SERVICES</li><li>NEWS</li><li>CONTACT US</li>
    </ul>
  </header>

  <section class="hero" role="img" aria-label="Bronze statue in a colonial town square">
    <div class="hero-caption">
      <div class="kicker">WE WILL BE</div>
      <div class="title">TARGETING TOURISM IN A SMALL TOWN IN CENTRAL PANAMA</div>
    </div>
    <div class="arrow prev"><svg width="14" height="14" viewBox="0 0 14 14"><path d="M9 2 L4 7 L9 12" stroke="#333" stroke-width="2" fill="none"/></svg></div>
    <div class="arrow next"><svg width="14" height="14" viewBox="0 0 14 14"><path d="M5 2 L10 7 L5 12" stroke="#333" stroke-width="2" fill="none"/></svg></div>
    <div class="dots"><span class="on"></span><span></span><span></span><span></span></div>
  </section>

  <h2 class="section-title">TOUR &amp; SITESEEING</h2>
  <p class="tour-links">Ship Show: <a>Bus &amp; Minivan Tours</a> | <a>City Tours</a> | <a>Full-day Tours</a> | <a>Hop-On Hop-Off</a> | <a>Night Tour</a> | <a>Segway Tours</a> | <a>Self Guided Tours &amp; Island Hopper Tours</a></p>

  <div class="cards">
    <article class="card"><div class="photo p1" role="img" aria-label="Rock arch over the sea"></div><div class="body"><h3>El Arco Rock Formation in Mexico with boats on the water</h3><div class="rating"><span class="stars">★★★★☆</span>646 Reviews</div><div class="viewer">Viewer: Usc</div><div class="price">from USD<strong>$79.99</strong></div></div></article>
    <article class="card"><div class="photo p2" role="img" aria-label="Stacked timber logs"></div><div class="body"><h3>El Arco Rock Formation in Mexico with boats on the water</h3><div class="rating"><span class="stars">★★★★☆</span>646 Reviews</div><div class="viewer">Viewer: Usc</div><div class="price">from USD<strong>$79.99</strong></div></div></article>
    <article class="card"><div class="photo p3" role="img" aria-label="River through green forest"></div><div class="body"><h3>El Arco Rock Formation in Mexico with boats on the water</h3><div class="rating"><span class="stars">★★★★☆</span>646 Reviews</div><div class="viewer">Viewer: Usc</div><div class="price">from USD<strong>$79.99</strong></div></div></article>
    <article class="card"><div class="photo p4" role="img" aria-label="Historic palace at dusk"></div><div class="body"><h3>El Arco Rock Formation in Mexico with boats on the water</h3><div class="rating"><span class="stars">★★★★☆</span>646 Reviews</div><div class="viewer">Viewer: Usc</div><div class="price">from USD<strong>$79.99</strong></div></div></article>
    <article class="card"><div class="photo p5" role="img" aria-label="Waterfront city skyline"></div><div class="body"><h3>El Arco Rock Formation in Mexico with boats on the water</h3><div class="rating"><span class="stars">★★★★☆</span>646 Reviews</div><div class="viewer">Viewer: Usc</div><div class="price">from USD<strong>$79.99</strong></div></div></article>
    <article class="card"><div class="photo p6" role="img" aria-label="White colonial building under blue sky"></div><div class="body"><h3>El Arco Rock Formation in Mexico with boats on the water</h3><div class="rating"><span class="stars">★★★★☆</span>646 Reviews</div><div class="viewer">Viewer: Usc</div><div class="price">from USD<strong>$79.99</strong></div></div></article>
    <article class="card"><div class="photo p7" role="img" aria-label="Hilltop monument against the sky"></div><div class="body"><h3>El Arco Rock Formation in Mexico with boats on the water</h3><div class="rating"><span class="stars">★★★★☆</span>646 Reviews</div><div class="viewer">Viewer: Usc</div><div class="price">from USD<strong>$79.99</strong></div></div></article>
    <article class="card"><div class="photo p8" role="img" aria-label="Old stone bridge over a river"></div><div class="body"><h3>El Arco Rock Formation in Mexico with boats on the water</h3><div class="rating"><span class="stars">★★★★☆</span>646 Reviews</div><div class="viewer">Viewer: Usc</div><div class="price">from USD<strong>$79.99</strong></div></div></article>
  </div>

  <div class="columns">
    <section>
      <h3 class="col-title"><svg width="16" height="20" viewBox="0 0 16 20"><path d="M8 0C3.6 0 0 3.4 0 7.6 0 13 8 20 8 20s8-7 8-12.4C16 3.4 12.4 0 8 0z" fill="var(--orange)"/><circle cx="8" cy="7.5" r="3" fill="#fff"/></svg>HOT DESTINATIONS</h3>
      <div class="dest">
        <ul><li>Paris</li><li>Las Vegas</li><li>Rome</li><li>New York City</li><li>London</li><li>Amsterdam</li><li>Barcelona</li></ul>
        <ul><li>Florence</li><li>Venice</li><li>Milan</li><li>San Francisco</li><li>Tokyo</li><li>Sydney</li><li>Melbourne</li></ul>
      </div>
    </section>
    <section class="beat">
      <h3 class="col-title"><svg width="18" height="18" viewBox="0 0 18 18"><rect width="18" height="18" fill="var(--orange)"/><text x="9" y="14" font-size="13" font-weight="700" fill="#fff" text-anchor="middle" font-family="Open Sans,sans-serif">$</text></svg>BEAT THE BEST PRICES</h3>
      <p>Lorem ipsum dolor sit amet, consectetur adipiscing elit, sed do eiusmod tempor incididunt ut labore et dolore magna aliqua.</p>
      <div class="row">
        <div class="thumb" role="img" aria-label="Travel deal photo"></div>
        <ul class="deals"><li>Exceptour sint</li><li>Occaecat</li><li>Cupidatat non</li><li>Proident</li></ul>
      </div>
    </section>
    <section>
      <h3 class="col-title"><svg width="18" height="18" viewBox="0 0 18 18"><rect y="4" width="18" height="14" fill="var(--orange)"/><rect x="6" y="0" width="6" height="5" fill="none" stroke="var(--orange)" stroke-width="2"/></svg>INSIDERS PICKS</h3>
      <ul class="picks">
        <li>✓ Exceptour sint</li><li>✓ Occaecat</li><li>✓ Cupidatat non</li><li>✓ Proident</li><li>✓ Exceptour sint</li><li>✓ Occaecat</li><li>✓ Cupidatat non</li>
      </ul>
    </section>
  </div>
</div>

<footer class="footer">
  <div class="f-brand">
    <div class="f-badge"></div>
    <div>
      <h4>Mileage program</h4>
      <p>Earn points on every trip and redeem them for tours, stays and local dining around town.</p>
      <p class="more">LEARN MORE</p>
    </div>
  </div>
  <div class="f-col">
    <h4>Useful Links</h4>
    <ul><li>About Us</li><li>Corporate Info</li><li>Media Center</li><li>Careers</li><li>Site Map</li><li>Free Newsletter</li></ul>
  </div>
  <div class="f-col">
    <h4>Support</h4>
    <ul><li>Customer Care</li><li>Privacy Policy</li><li>Low Price Guarantee</li><li>Group Services</li><li>Mileage Program</li></ul>
  </div>
  <div class="f-follow">
    <h4>Follow Us</h4>
    <div class="social"><span></span><span></span><span></span><span></span></div>
    <p class="copy">© 2015 - Caldera Key. All<br>Right Reserved</p>
  </div>
</footer>
</body>
</html>
```